Business Card Design for Occupational Medicine Start Up Company

We need to design a professional business card. We are a healthcare company providing occupational medicine services to blue collar industries. We are professional, efficient and high quality service providers.

Target Market(s)

Blue Collar Industry: Shipbuilding, Ports, Trucking Companies; The Executives and Safety Officers for these companies

Industry/Entity Type

Healthcare

Contact Information for Business Card

Logo, Name, Title, Email, Phone

Other font styles liked:
• Please match our Brand Guide

Requirements
Must have
• Our Company Colors and Logo

```html
<!DOCTYPE html>
<html lang="en">
<head>
<meta charset="utf-8">
<title>CrewWell Clinics – Business Card</title>
<link href="https://fonts.googleapis.com/css2?family=Arimo:wght@400;700&display=swap" rel="stylesheet">
<style>
  :root{
    --page-bg:#e7e4df;
    --navy-light:#3b4687;
    --navy-deep:#0b1040;
    --frost-light:#f3f4f5;
    --frost-dark:#dde1e4;
    --accent-orange:#e98a24;
    --accent-blue:#2a8fcf;
    --text-light:#dfe2ee;
    --icon-blue:#5f86c2;
    --brand-ink:#161a3f;
  }
  html,body{margin:0;padding:0;width:1200px;height:969px;overflow:hidden;background:var(--page-bg);}
  .canvas{position:relative;width:1200px;height:969px;}
  .card{
    position:absolute;left:140px;top:222px;width:920px;height:525px;
    border-radius:24px;overflow:hidden;
    box-shadow:0 14px 40px rgba(0,0,0,.18);
    font-family:"Arimo",Arial,sans-serif;
  }
  .card-art{position:absolute;inset:0;}
  .contact-block{position:absolute;left:51px;top:116px;color:var(--text-light);}
  .person-name{margin:0;font-size:27px;font-weight:700;color:var(--accent-blue);letter-spacing:.3px;}
  .person-title{margin:4px 0 0;font-size:19px;}
  .address{margin:32px 0 0;font-size:19px;line-height:25px;}
  .contact-list{list-style:none;margin:12px 0 0;padding:0;font-size:19px;line-height:26px;}
  .contact-list li{display:flex;align-items:center;gap:10px;}
  .contact-list svg{width:15px;height:15px;fill:var(--icon-blue);flex:none;}
  .brand-name{
    position:absolute;left:400px;width:520px;top:292px;margin:0;text-align:center;
    font-size:36px;font-weight:700;color:var(--brand-ink);letter-spacing:1px;
  }
</style>
</head>
<body>
<div class="canvas">
  <div class="card">
    <svg class="card-art" width="920" height="525" viewBox="0 0 920 525" aria-hidden="true">
      <defs>
        <linearGradient id="navyPanel" x1="0" y1="0" x2="1" y2="0.4">
          <stop offset="0" stop-color="var(--navy-light)"/>
          <stop offset="0.6" stop-color="#1e2663"/>
          <stop offset="1" stop-color="var(--navy-deep)"/>
        </linearGradient>
        <linearGradient id="frostPanel" x1="0" y1="0" x2="1" y2="1">
          <stop offset="0" stop-color="var(--frost-light)"/>
          <stop offset="1" stop-color="var(--frost-dark)"/>
        </linearGradient>
      </defs>
      <rect class="frost-panel" width="920" height="525" fill="url(#frostPanel)"/>
      <polygon class="navy-panel" points="0,0 600,0 346,266 588,525 0,525" fill="url(#navyPanel)"/>
      <path class="accent-line-orange" d="M612 0 L360 262 Q352 270 360 278" fill="none" stroke="var(--accent-orange)" stroke-width="5"/>
      <path class="accent-line-blue" d="M350 262 Q342 272 352 284 L594 525" fill="none" stroke="var(--accent-blue)" stroke-width="5"/>
      <circle class="punch-hole" cx="383" cy="266" r="12" fill="var(--navy-deep)"/>
    </svg>

    <div class="contact-block">
      <h1 class="person-name">Daniel Reyes</h1>
      <p class="person-title">President</p>
      <p class="address">4120 Harbor View Road<br>Seward, Alaska 99664</p>
      <ul class="contact-list">
        <li><svg viewBox="0 0 16 16"><path d="M3 1l3 3-1.5 2a9 9 0 0 0 5.5 5.5L12 10l3 3-2 2C7 15 1 9 1 3z"/></svg>555-014-2837</li>
        <li><svg viewBox="0 0 16 16"><path d="M4 0h8a1 1 0 0 1 1 1v14a1 1 0 0 1-1 1H4a1 1 0 0 1-1-1V1a1 1 0 0 1 1-1zm1 2v10h6V2z"/></svg>555-019-4602</li>
        <li><svg viewBox="0 0 16 16"><path d="M4 1h8v4H4zM1 6h14v7h-3v2H4v-2H1zm4 5v3h6v-3z"/></svg>555-017-3391</li>
        <li><svg viewBox="0 0 16 16"><path d="M1 3h14v10H1zm1 1.5V5l6 4 6-4v-.5z"/></svg>hello@crewwellmed.com</li>
        <li><svg viewBox="0 0 16 16"><circle cx="8" cy="8" r="7"/></svg>www.crewwellmed.com</li>
      </ul>
    </div>

    <p class="brand-name">CREWWELL CLINICS</p>
  </div>
</div>
</body>
</html>
```